Timber Crest Construction Needs business card

Hey we are in need of business card designs. I have upload our logo as a guideline, but free feel to run with it or come up with something unique.
Pls have fun with it and be creative. the name says it all!
i will give some directions after i see a few entries..
Updates
Logo source file has been uploaded..
Hey because of the logo is so colourful already.
Can we have a few submissions with less colour.
Also we are looking for clever/hidden/descriptive business card.

```html
<!DOCTYPE html>
<html lang="en">
<head>
<meta charset="utf-8">
<title>Timber Crest Construction — Business Card</title>
<link rel="stylesheet" href="https://fonts.googleapis.com/css2?family=Arimo:wght@400;700&display=swap">
<style>
  :root {
    --stage: #e9e6e2;
    --card: #ffffff;
    --ink: #1e1e1e;
    --brand-grey: #5b6062;
    --band-grey: #5f6466;
    --band-text: #ffffff;
    --rule-light: #dfe6ee;
  }
  * { margin: 0; padding: 0; box-sizing: border-box; }
  html, body { width: 1200px; height: 470px; overflow: hidden; }
  body {
    background: var(--stage);
    font-family: "Arimo", Arial, sans-serif;
    color: var(--ink);
    position: relative;
  }
  .card {
    position: absolute;
    top: 80px;
    width: 540px;
    height: 310px;
    background: var(--card);
    box-shadow: 0 6px 18px rgba(0,0,0,0.18);
    overflow: hidden;
  }
  .card--front { left: 40px; }
  .card--back { left: 620px; }

  .wordmark {
    position: absolute;
    left: 0; right: 0;
    text-align: center;
    color: var(--brand-grey);
    font-weight: 700;
    line-height: 1;
  }
  .card--front .wordmark { top: 58px; }
  .wordmark__name { display: block; font-size: 38px; letter-spacing: -0.5px; }
  .wordmark__sub { display: block; font-size: 11px; letter-spacing: 1px; margin-top: 4px; }
  .wordmark__square {
    display: inline-block;
    width: 22px; height: 22px;
    background: var(--brand-grey);
    margin-bottom: 10px;
  }

  .contact {
    position: absolute;
    left: 0; right: 0;
    top: 150px;
    text-align: center;
    font-size: 14px;
    line-height: 24px;
  }
  .contact__row { display: flex; justify-content: center; gap: 14px; }
  .contact__item { display: inline-flex; align-items: center; gap: 4px; }
  .icon { width: 12px; height: 12px; fill: none; stroke: var(--ink); stroke-width: 1.6; }

  .band { position: absolute; left: 0; bottom: 0; width: 540px; height: 90px; }
  .holder {
    position: absolute;
    left: 0; right: 0;
    bottom: 16px;
    text-align: center;
    color: var(--band-text);
    font-size: 20px;
  }
  .holder__title { font-size: 15px; }

  .card--back .wordmark { top: 96px; }
  .card--back .wordmark__name { font-size: 44px; }
  .card--back .wordmark__sub { font-size: 12px; }
  .back-url {
    position: absolute;
    left: 0; right: 0;
    top: 172px;
    text-align: center;
    font-size: 19px;
  }
  .back-rules { position: absolute; left: 0; bottom: 18px; width: 540px; height: 20px; }
</style>
</head>
<body>
  <section class="card card--front">
    <div class="wordmark">
      <span class="wordmark__square"></span>
      <span class="wordmark__name">TIMBER CREST</span>
      <span class="wordmark__sub">CONSTRUCTION</span>
    </div>

    <div class="contact">
      <div class="contact__row">
        <span class="contact__item">
          <svg class="icon" viewBox="0 0 12 12"><path d="M3 1 L5 3.5 L4 5 Q5 7 7 8 L8.5 7 L11 9 L9.5 11 Q3 10 1 2.5 Z"/></svg>0400 555 018
        </span>
        <span class="contact__item">
          <svg class="icon" viewBox="0 0 12 12"><path d="M3 1 L5 3.5 L4 5 Q5 7 7 8 L8.5 7 L11 9 L9.5 11 Q3 10 1 2.5 Z"/></svg>0400 555 018
        </span>
      </div>
      <div class="contact__row">
        <span class="contact__item">hello@timbercrestbuild.com</span>
        <span class="contact__item">
          <svg class="icon" viewBox="0 0 12 12"><circle cx="6" cy="6" r="5"/><path d="M1 6 H11 M6 1 Q3 6 6 11 M6 1 Q9 6 6 11"/></svg>www.timbercrestbuild.com
        </span>
      </div>
      <div class="contact__row">
        <span class="contact__item">
          <svg class="icon" viewBox="0 0 12 12"><rect x="1" y="3" width="10" height="7"/><path d="M1 3 L6 7 L11 3"/></svg>Street Name City Name, State Zipcode
        </span>
      </div>
    </div>

    <svg class="band" viewBox="0 0 540 90" preserveAspectRatio="none" aria-hidden="true">
      <path d="M0 32 Q270 -6 540 8 L540 90 L0 90 Z" fill="var(--band-grey)"/>
      <path d="M0 26 Q270 -12 540 2" fill="none" stroke="var(--ink)" stroke-width="1.5"/>
    </svg>
    <div class="holder">Your Name, <span class="holder__title">Title</span></div>
  </section>

  <section class="card card--back">
    <div class="wordmark">
      <span class="wordmark__name">TIMBER CREST</span>
      <span class="wordmark__sub">CONSTRUCTION</span>
    </div>
    <div class="back-url">www.timbercrestbuild.com</div>
    <svg class="back-rules" viewBox="0 0 540 20" aria-hidden="true">
      <line x1="0" y1="4" x2="540" y2="2" stroke="var(--rule-light)" stroke-width="3"/>
      <line x1="0" y1="14" x2="540" y2="12" stroke="var(--rule-light)" stroke-width="2"/>
    </svg>
  </section>
</body>
</html>
```